Web design for Crowdfunding site HopeWingsRally.com

We need a web design for christian crowdfunding website. Here is the challenge: We need responsive layout that is targeted first in iPad size of screen. It should also scale somehow down to iPhone size of screens. Web layout can be about the same size as iPad screen.

Screens should work so that main page scrolls not but only certain part of the screen scrolls and always one "page" at time. We can implement these "scrolls" then later with javascript but now we need only design. The challenge is to create this kind of hybrid website / app look.

Target is at first to raise funds to orphan people needing about $40 per month for their living and education. There is always some organization which takes care of these kids. Later there will be other christian missions included. At first we are looking to find monthly supporters.

You can be as creative as you want :) As you see from the look and feel sector, I am not looking any same traditional look which many "help kids" sites have. I am looking to reach now younger generation and therefore iPad and mobile are the main screen sizes.

Inspirational designs:
- https://example-gallery.test/profiles/studiofernlake/designs/482716?from=%2Fbrowse%2Fxhr%2Fdesigns%3Fcategory%3Dmobile-app-design
- http://www.artpoolhub.test/design/8261047 Clear, simple visuals
- http://www.artpoolhub.test/design/7394215 Header
- http://www.artpoolhub.test/design/6048392 Contrast in the colors, i think is powerfull

Some terms could be: Kids play, kids are learning (in the school). No static posture but living like kids are. I wonder also how we could also add little bit gaming style even though the question is of reali life of real people. Giving should be rewarding.

Target Market(s)

People who want help other people.

Industry/Entity Type

Christian

Number of Pages Required

4 page

Requirements
Must have
• Homepage. Mission page (In my wireframes it was one kid).
Nice to have
• Other pages and some idea how to scroll. 4 pages is no must. If you feel easy, please give first some draft and I give comments on that.

```html
<!DOCTYPE html>
<html lang="en">
<head>
<meta charset="utf-8">
<title>HopeWingsRally – Mission</title>
<link rel="stylesheet" href="https://fonts.googleapis.com/css2?family=Mulish:wght@400;500;600&family=Open+Sans:wght@400;600&display=swap">
<style>
:root{
  --yellow:#ffc300;
  --ink:#1c1c1c;
  --bg-dark:#2f2f2f;
  --panel:rgba(40,40,40,.82);
  --row:rgba(72,72,72,.9);
  --muted:#c9c9c9;
  --soft:#9a9a9a;
  --footer:#232323;
  --head:'Mulish',sans-serif;
  --body:'Open Sans',sans-serif;
}
*{box-sizing:border-box;margin:0;padding:0}
html,body{width:1200px;height:720px;overflow:hidden}
body{position:relative;background:var(--bg-dark);font-family:var(--body);color:#fff}
.backdrop{position:absolute;left:0;top:64px;width:1200px;height:616px;
  background:radial-gradient(ellipse at 35% 40%,#5b5b5b 0%,#3e3e3e 45%,#262626 100%)}
.topbar{position:absolute;left:0;top:0;width:1200px;height:64px;background:var(--yellow);color:var(--ink);font-family:var(--head)}
.menu-link{position:absolute;left:190px;top:21px;font-size:17px;font-weight:500;display:flex;align-items:center;gap:10px}
.search-btn{position:absolute;left:374px;top:16px;width:33px;height:33px;border:1px solid var(--ink);border-radius:2px;display:flex;align-items:center;justify-content:center}
.brand{position:absolute;left:0;width:1200px;top:12px;text-align:center;font-size:33px;font-weight:500;letter-spacing:.3px}
.auth{position:absolute;top:15px;height:34px;border:1px solid var(--ink);border-radius:2px;font-size:14px;display:flex;align-items:center;justify-content:center}
.auth.login{left:854px;width:73px}.auth.signup{left:935px;width:73px}
.rail{position:absolute;left:192px;top:92px;width:4px;height:558px;background:#8a8a8a}
.rail::before{content:"";position:absolute;left:-2px;top:0;width:5px;height:5px;background:#fff}
.rail::after{content:"";position:absolute;left:-2px;bottom:0;width:5px;height:5px;background:#fff}
.rail-mark{position:absolute;left:191px;top:425px;width:6px;height:5px;background:var(--yellow)}
.title{position:absolute;left:208px;top:86px;font-family:var(--head);font-size:26px;font-weight:600}
.share{position:absolute;top:96px;display:flex;gap:20px;left:888px}
.share span{width:14px;height:14px;border-radius:50%;background:#bdbdbd;display:block}
.tabs{position:absolute;left:206px;top:129px;width:520px;border-top:3px solid var(--yellow);display:flex;font-family:var(--head);font-size:17px;font-weight:500}
.tab{height:37px;display:flex;align-items:center;padding:0 19px}
.tab.active{background:var(--yellow);color:var(--ink);width:96px;justify-content:center;padding:0}
.story{position:absolute;left:207px;width:522px;font-size:10.6px;line-height:19.2px;color:var(--muted)}
.story p+p{margin-top:19px}
.photo{position:absolute;left:207px;top:354px;width:520px;height:160px;
  background:linear-gradient(180deg,#6f7c93 0%,#a48e8a 45%,#d99a6b 75%,#f0b37b 100%)}
.card{position:absolute;left:752px;top:128px;width:256px;height:526px;background:var(--panel);border:1px solid #555}
.card .who{padding:15px 15px 0}
.card h2{font-family:var(--head);font-size:18px;font-weight:600}
.meta{font-size:10.5px;color:var(--muted);margin-top:6px;line-height:17px}
.sep{position:absolute;left:0;width:254px;height:1px;background:#555}
.support{position:absolute;top:100px;left:15px;display:flex;align-items:center;font-size:11px;color:var(--muted)}
.support .av{width:24px;height:24px;border-radius:50%;background:#b9a595;border:2px solid #eee;margin-left:8px}
.support .av:first-of-type{margin-left:15px}
.mine{position:absolute;top:153px;left:16px;font-size:12.5px;color:var(--yellow)}
.ring{position:absolute;left:16px;top:180px}
.given{position:absolute;left:90px;top:183px}
.given b{font-weight:400;font-size:13px}
.given small{display:block;font-size:10.5px;color:var(--muted);margin-top:2px}
.given .need{display:flex;align-items:center;gap:8px;font-size:13px;margin-top:8px}
.part{position:absolute;top:277px;left:16px;font-size:13px;color:var(--yellow)}
.options{position:absolute;left:2px;top:297px;width:250px}
.opt{height:43px;background:var(--row);margin-bottom:3px;display:flex;align-items:center;padding:0 12px 0 16px;font-size:13px;color:#ddd;position:relative}
.opt .chk{width:28px;height:28px;background:#8c8c8c;margin-right:12px;border-radius:1px}
.opt svg{position:absolute;right:12px;top:15px}
.opt .amt{position:absolute;left:128px;top:5px;width:86px;height:34px;background:#5c5c5c;font-size:10.5px;color:#aaa;display:flex;align-items:center;padding-left:8px}
.footer{position:absolute;left:0;top:680px;width:1200px;height:40px;background:var(--footer)}
.copy{position:absolute;left:190px;top:13px;font-size:11.5px;color:#ddd}
.foot-social{position:absolute;left:832px;top:14px;display:flex;gap:20px}
.foot-social span{width:14px;height:14px;border-radius:50%;background:#cfcfcf;display:block}
</style>
</head>
<body>
<div class="backdrop" role="img" aria-label="Dim background photo of people holding hands"></div>

<header class="topbar">
  <div class="menu-link">
    <svg width="15" height="12" viewBox="0 0 15 12"><rect width="15" height="2.4" fill="#1c1c1c"/><rect y="4.8" width="15" height="2.4" fill="#1c1c1c"/><rect y="9.6" width="15" height="2.4" fill="#1c1c1c"/></svg>
    See the missions
  </div>
  <div class="search-btn"><svg width="15" height="15" viewBox="0 0 15 15"><circle cx="6" cy="6" r="4.5" fill="none" stroke="#1c1c1c" stroke-width="2"/><line x1="9.3" y1="9.3" x2="13.5" y2="13.5" stroke="#1c1c1c" stroke-width="2.4"/></svg></div>
  <div class="brand">HopeWingsRally</div>
  <div class="auth login">Log In</div>
  <div class="auth signup">Sign Up</div>
</header>

<div class="rail"></div><div class="rail-mark"></div>
<h1 class="title">Mission : Orphan Maria, 11y</h1>
<div class="share"><span></span><span></span><span></span><span></span></div>

<nav class="tabs">
  <div class="tab active">Story</div><div class="tab">Updates</div><div class="tab">Comments</div>
</nav>

<div class="story" style="top:185px">
  <p>Aenean fermentum felis sem, a elementum erat aliquet sed. In purus mauris, rutrum et eros vel, elementum laoreet ipsum. Sed a placerat dui. Suspendisse ac lectus eget augue pulvinar placerat id sed mi. Class aptent taciti sociosqu ad litora torquent per conubia nostra, per inceptos himenaeos. Donec tempor lorem in massa varius, ac hendrerit diam imperdiet. Ut sit amet blandit arcu. Cras ut consectetur ante. Phasellus hendrerit, ipsum a mollis sollicitudin, elit tellus ornare dui.</p>
  <p>Donec eu neque id mauris sodales faucibus non eget nisi. Quisque facilisis id nunc porttitor imperdiet. Suspendisse volutpat vel orci fringilla mattis. Pellentesque ut blandit augue.</p>
</div>
<div class="photo" role="img" aria-label="Photo of a girl jumping at sunset holding red balloons"></div>
<div class="story" style="top:542px;left:209px">
  <p>Aenean fermentum felis sem, a elementum erat aliquet sed. In purus mauris, rutrum et eros vel, elementum laoreet ipsum. Sed a placerat dui. Suspendisse ac lectus eget augue pulvinar placerat id sed mi. Class aptent taciti sociosqu ad litora torquent per conubia nostra, per inceptos himenaeos. Donec tempor lorem in massa varius, ac hendrerit diam imperdiet. Donec eu neque id mauris sodales faucibus non eget nisi. Quisque facilisis id nunc porttitor imperdiet. Suspendisse volutpat vel orci fringilla mattis. Pellentesque ut blandit augue. Phasellus blandit neque eu nisl ornare, vel aliquam tellus cursus.</p>
</div>

<aside class="card">
  <div class="who">
    <h2>Name : Maria, 11y</h2>
    <div class="meta">
      <svg width="7" height="10" viewBox="0 0 7 10"><path d="M3.5 0A3.5 3.5 0 0 0 0 3.5C0 6 3.5 10 3.5 10S7 6 7 3.5A3.5 3.5 0 0 0 3.5 0z" fill="#bbb"/><circle cx="3.5" cy="3.5" r="1.3" fill="#333"/></svg>
      &nbsp;Kalkutta<br>Organization : Harbor Trust
    </div>
  </div>
  <div class="sep" style="top:89px"></div>
  <div class="support">Support
    <span class="av" role="img" aria-label="Supporter avatar"></span><span class="av" role="img" aria-label="Supporter avatar"></span><span class="av" role="img" aria-label="Supporter avatar"></span><span class="av" role="img" aria-label="Supporter avatar"></span><span class="av" role="img" aria-label="Supporter avatar"></span>
    <svg style="margin-left:12px" width="7" height="11" viewBox="0 0 7 11"><path d="M1 1l4.5 4.5L1 10" fill="none" stroke="#bbb" stroke-width="1.8"/></svg>
  </div>
  <div class="sep" style="top:133px"></div>
  <div class="mine">My Support is now : $5 / month <span style="color:#bbb">✖</span></div>
  <svg class="ring" width="62" height="62" viewBox="0 0 62 62">
    <circle cx="31" cy="31" r="27" fill="none" stroke="#8a8a8a" stroke-width="5"/>
    <circle cx="31" cy="31" r="27" fill="none" stroke="#ffc300" stroke-width="5" stroke-dasharray="76.3 170" transform="rotate(-90 31 31)"/>
    <text x="29" y="37" text-anchor="middle" fill="#fff" font-family="Mulish,sans-serif" font-size="17" font-weight="600">45<tspan font-size="8" dy="-6">%</tspan></text>
  </svg>
  <div class="given"><b>$15 given</b><small>of total $35 needed</small>
    <div class="need"><svg width="12" height="12" viewBox="0 0 12 12"><rect x="0.5" y="1.5" width="11" height="10" fill="none" stroke="#aaa"/><path d="M0.5 4h11M4 4v7.5M8 4v7.5M0.5 7.7h11" stroke="#aaa"/></svg>per month need</div>
  </div>
  <div class="sep" style="top:257px"></div>
  <div class="part">Participate</div>
  <div class="options">
    <div class="opt"><span class="chk"></span>I am in, $1 / month<svg width="15" height="13" viewBox="0 0 15 13"><path d="M0 0h3l2 8h8l2-6H4" fill="#bbb"/><circle cx="6" cy="11" r="1.5" fill="#bbb"/><circle cx="12" cy="11" r="1.5" fill="#bbb"/></svg></div>
    <div class="opt"><span class="chk"></span>Increased, $5 / month<svg width="15" height="13" viewBox="0 0 15 13"><path d="M0 0h3l2 8h8l2-6H4" fill="#bbb"/><circle cx="6" cy="11" r="1.5" fill="#bbb"/><circle cx="12" cy="11" r="1.5" fill="#bbb"/></svg></div>
    <div class="opt"><span class="chk"></span>Decent help, $10 / month<svg width="15" height="13" viewBox="0 0 15 13"><path d="M0 0h3l2 8h8l2-6H4" fill="#bbb"/><circle cx="6" cy="11" r="1.5" fill="#bbb"/><circle cx="12" cy="11" r="1.5" fill="#bbb"/></svg></div>
    <div class="opt"><span class="chk"></span>Whole kid, $35 / month<svg width="15" height="13" viewBox="0 0 15 13"><path d="M0 0h3l2 8h8l2-6H4" fill="#bbb"/><circle cx="6" cy="11" r="1.5" fill="#bbb"/><circle cx="12" cy="11" r="1.5" fill="#bbb"/></svg></div>
    <div class="opt"><span class="chk"></span>My Amount<span class="amt">Enter amount</span><svg width="15" height="13" viewBox="0 0 15 13"><path d="M0 0h3l2 8h8l2-6H4" fill="#bbb"/><circle cx="6" cy="11" r="1.5" fill="#bbb"/><circle cx="12" cy="11" r="1.5" fill="#bbb"/></svg></div>
  </div>
</aside>

<footer class="footer">
  <div class="copy">Copyright &nbsp;©&nbsp; 2016 &nbsp;Hope Wings Rally. &nbsp;All rights reserved.</div>
  <div class="foot-social"><span></span><span></span><span></span><span></span><span></span><span></span></div>
</footer>
</body>
</html>
```